Software Development Consulting Company Needs Business Card Design

We need a new business card design for our consultants at Kestrel Works (kestrelworks.example). We are a small firm that provides high-end software development and methodology consulting to medium to large enterprise IT organizations.

Our logo uses Futura for the font and we would like to stick with navy blue and canary yellow for the logo colors. Attached are normal and reversed versions of our logos in illustrator format.
Updates

Hi Everyone, Thank yo very much for your amazing design ideas. I have created a poll for this project and our employees will be voting on the design they wish to use. We will be making a decision this Wednesday (October 22nd). Thanks again, Dale Hartwick

Industry/Entity Type

Business

```html
<!DOCTYPE html>
<html lang="en">
<head>
<meta charset="utf-8">
<title>Kestrel Works — Business Card</title>
<link rel="stylesheet" href="https://fonts.googleapis.com/css2?family=Jost:wght@400;500;600&display=swap">
<style>
  :root {
    --navy: #1f4571;
    --canary: #ffe500;
    --ink: #333a44;
    --muted: #5d6670;
    --divider: #b9c0c8;
    --card: #ffffff;
    --backdrop: #e9ebee;
  }
  * { box-sizing: border-box; margin: 0; padding: 0; }
  html, body {
    width: 1200px; height: 720px; overflow: hidden;
    background: var(--backdrop);
    font-family: "Jost", sans-serif;
  }
  .canvas {
    position: relative; width: 1200px; height: 720px;
  }
  .card {
    position: absolute; top: 205px;
    width: 540px; height: 309px;
    background: var(--card);
    box-shadow: 0 6px 18px rgba(0,0,0,.12);
    overflow: hidden;
  }
  .card--front { left: 40px; }
  .card--back { left: 620px; }

  /* Front */
  .brand {
    position: absolute; top: 38px; left: 0; right: 0;
    display: flex; align-items: center; justify-content: center; gap: 12px;
  }
  .brand__dot {
    width: 14px; height: 14px; border-radius: 50%;
    background: var(--canary);
  }
  .brand__name {
    font-weight: 500; color: var(--navy);
    font-size: 38px; letter-spacing: 3px; text-transform: uppercase;
  }
  .identity {
    position: absolute; top: 112px; left: 150px; width: 150px;
    text-align: right; padding-right: 14px;
  }
  .identity__name { font-weight: 600; font-size: 19px; color: var(--navy); }
  .identity__title { font-size: 13px; color: var(--muted); }
  .divider {
    position: absolute; top: 104px; left: 310px;
    width: 1px; height: 62px; background: var(--divider);
  }
  .contact {
    position: absolute; top: 104px; left: 322px;
    list-style: none; font-size: 13.5px; color: var(--ink); line-height: 21px;
  }
  .contact li { display: flex; align-items: center; gap: 7px; }
  .icon { width: 12px; height: 12px; flex: none; }
  .location {
    position: absolute; top: 188px; left: 40px;
    display: flex; align-items: center; gap: 6px;
    font-size: 13.5px; color: var(--ink);
  }
  .swoosh { position: absolute; left: 0; bottom: 0; width: 540px; height: 309px; }

  /* Back */
  .wordmark {
    position: absolute; top: 92px; left: 0; right: 0;
    text-align: center;
    font-weight: 500; color: var(--navy);
    font-size: 54px; letter-spacing: 6px; text-transform: uppercase;
  }
  .web-address {
    position: absolute; top: 206px; left: 0; right: 0;
    text-align: center; font-size: 19px; letter-spacing: 2.5px; color: var(--ink);
  }
</style>
</head>
<body>
<main class="canvas">

  <section class="card card--front" aria-label="Business card front">
    <svg class="swoosh" viewBox="0 0 540 309" aria-hidden="true">
      <path fill="var(--canary)" d="M0,262 C150,268 330,205 540,150 L540,164 C330,218 160,282 0,282 Z"/>
      <path fill="var(--navy)" d="M0,282 C160,282 330,218 540,164 L540,190 C360,232 200,300 120,309 L0,309 Z"/>
      <path fill="var(--canary)" d="M0,296 C40,300 80,304 120,309 L0,309 Z"/>
    </svg>

    <div class="brand">
      <span class="brand__dot"></span>
      <span class="brand__name">Kestrel Works</span>
    </div>

    <div class="identity">
      <p class="identity__name">Your Name</p>
      <p class="identity__title">Title</p>
    </div>
    <span class="divider"></span>
    <ul class="contact">
      <li>
        <svg class="icon" viewBox="0 0 12 12" aria-hidden="true"><circle cx="6" cy="6" r="5.3" fill="none" stroke="var(--navy)" stroke-width="1.2"/><path d="M4 3.2l1 .1.6 1.5-.7.6c.4.8.9 1.3 1.7 1.7l.6-.7 1.5.6.1 1c-2.6.6-5.1-1.9-4.8-4.8z" fill="var(--navy)"/></svg>
        012-555-0148
      </li>
      <li>
        <svg class="icon" viewBox="0 0 12 12" aria-hidden="true"><rect x="1" y="2.5" width="10" height="7" rx="1" fill="var(--navy)"/><path d="M1.5 3.2L6 6.6l4.5-3.4" fill="none" stroke="#fff" stroke-width="1"/></svg>
        info@kestrelworks.example
      </li>
      <li>
        <svg class="icon" viewBox="0 0 12 12" aria-hidden="true"><circle cx="6" cy="6" r="5.2" fill="none" stroke="var(--navy)" stroke-width="1.1"/><ellipse cx="6" cy="6" rx="2.3" ry="5.2" fill="none" stroke="var(--navy)" stroke-width="1"/><path d="M.8 6h10.4" stroke="var(--navy)" stroke-width="1"/></svg>
        www.kestrelworks.example
      </li>
    </ul>

    <p class="location">
      <svg class="icon" viewBox="0 0 12 12" aria-hidden="true"><path d="M6 .8a3.8 3.8 0 0 0-3.8 3.8C2.2 7.4 6 11.4 6 11.4s3.8-4 3.8-6.8A3.8 3.8 0 0 0 6 .8z" fill="var(--navy)"/><circle cx="6" cy="4.6" r="1.4" fill="#fff"/></svg>
      Ashford, Millbrook, IL
    </p>
  </section>

  <section class="card card--back" aria-label="Business card back">
    <p class="wordmark">Kestrel Works</p>
    <p class="web-address">www.kestrelworks.example</p>
  </section>

</main>
</body>
</html>
```